Agency Website & Personal brand

My name is Petros Vandelis & I've been a digital marketer & an e-commerce expert since 2010.

- I've spoken to 20 different events around the world up to 3,000 people in size.
- I've sold over 1500 training courses around e-commerce growth.
- I have over 100 testimonials (video & photo) from successful students who bought my training
- I have dozens of video testimonials from respected entrepreneurs that vouch for me and my work
- I have photos with marketing legends with that I shared the stage like Omar Lindqvist, Harold Venturini, Kyle Marsh & more
- I am the host of the Aegean Roundtable since 2017 - a high-level networking event for 7 & 8 figure entrepreneurs - 100 people have come to Greece since 2017
- I have tons of videos created where I showcase my expertise on growth
- I have worked with dozens of e-commerce stores on their growth & helped them scale to multiple 6, 7 & 8 figures either on consulting

I need a website design that showcases my authority & be a lead generating machine.

The goal is to bring people on a call with me but also grab their email and start building the relationship with them and free valuable content

We have 3 offers :

1. Paid ads (Done for You)
2. Consulting/Mastermind (Done with You)
3. Training (Do it Yourself)

```html
<!DOCTYPE html>
<html lang="en">
<head>
<meta charset="utf-8">
<title>Petros Vandelis — Digital Marketer &amp; E-commerce Expert</title>
<link rel="stylesheet" href="https://fonts.googleapis.com/css2?family=Oswald:wght@400;500;600&family=Lato:wght@400;700&display=swap">
<style>
:root{
  --blue:#1eb4ec;
  --ink:#111111;
  --black:#0d0d0d;
  --light:#f2f2f2;
  --white:#ffffff;
  --gold:#f5b71e;
  --head:'Oswald',sans-serif;
  --body:'Lato',sans-serif;
}
*{box-sizing:border-box;margin:0;padding:0}
html,body{width:1200px;height:2718px;overflow:hidden}
body{position:relative;background:var(--white);font-family:var(--body);color:var(--ink)}
.abs{position:absolute}

/* hero */
.hero{left:0;top:0;width:1200px;height:502px;background:linear-gradient(90deg,#0b1a4a 0%,#14286b 25%,#1a1a24 55%,#0c0c10 100%)}
.hero-scene{left:0;top:0;width:1200px;height:502px;background:radial-gradient(ellipse at 40% 35%,rgba(120,130,160,.35),transparent 45%),linear-gradient(180deg,transparent 60%,rgba(60,40,30,.55) 100%)}
.site-header{left:0;top:0;width:1200px;height:77px;background:rgba(10,12,20,.78)}
.brand{display:flex;align-items:center;gap:12px;font-family:var(--head);font-weight:500;font-size:36px;color:var(--white);letter-spacing:.2px;line-height:1}
.brand-mark{width:34px;height:40px;background:var(--blue)}
.nav{top:28px;display:flex;font-family:var(--head);font-size:15px;color:var(--white)}
.nav a{position:absolute;color:var(--white);text-decoration:none;white-space:nowrap}
.nav a.active{font-weight:600;text-decoration:underline;text-underline-offset:5px}
.pill{background:var(--blue);color:var(--white);font-family:var(--head);font-weight:500;border-radius:24px;display:flex;align-items:center;justify-content:center;box-shadow:3px 4px 0 rgba(0,0,0,.08)}
.hero-title{left:470px;top:152px;font-family:var(--head);font-weight:600;font-size:47px;line-height:60px;color:var(--white);text-transform:uppercase}

/* lead form */
.lead-band{left:0;top:502px;width:1200px;height:117px;background:var(--blue)}
.field{top:535px;width:176px;height:54px;background:var(--white);border-radius:6px;font-family:var(--head);font-size:14px;color:#333;display:flex;align-items:center;padding-left:18px}
.field.submit{justify-content:center;padding:0;font-weight:500;color:var(--ink)}
.caret{position:absolute;right:12px;top:24px;border:4px solid transparent;border-top:5px solid #222}

/* about */
.about{left:0;top:619px;width:1200px;height:572px;background:var(--light);overflow:hidden}
.section-title{font-family:var(--head);font-weight:600;font-size:44px;line-height:1;text-transform:uppercase;color:var(--ink)}
.about-text{left:111px;top:121px;width:485px;font-size:15px;line-height:27.5px;color:#222}
.about-text p+p{margin-top:27px;text-align:justify}

/* services */
.card{top:1306px;width:310px;height:302px}
.card-label{position:absolute;left:50%;transform:translateX(-50%);bottom:19px;background:var(--white);font-family:var(--head);font-weight:500;font-size:19px;padding:7px 16px;white-space:nowrap}

/* testimonials */
.reviews{left:0;top:1674px;width:1200px;height:651px;background:var(--light)}
.video{left:113px;top:1785px;width:574px;height:357px;border:2px solid var(--blue);background:linear-gradient(180deg,#e4e4e2 0%,#d2d2d0 55%,#6b6f78 100%)}
.review-text{left:722px;top:1794px;width:345px;font-size:15.5px;line-height:27.5px;color:#222}
.quote{left:888px;top:1908px;width:206px;text-align:center;font-size:13.5px;line-height:22px;color:#222}
.stars{left:722px;top:2053px;font-size:22px;color:var(--gold);letter-spacing:-1px}
.thumb{top:2175px;width:148px;height:89px;background:linear-gradient(135deg,#4a4a4e,#7a756f)}
.thumb.current{border:2px solid var(--blue);background:linear-gradient(135deg,#c9c9c7,#5d6170)}

/* footer */
.footer{left:0;top:2325px;width:1200px;height:393px;background:var(--ink)}
.social{top:2458px;width:31px;height:31px;border-radius:50%;background:var(--white)}
.col-title{top:2398px;font-family:var(--head);font-weight:500;font-size:21px;color:var(--white)}
.links{list-style:none;top:2437px;font-size:15px;color:var(--white)}
.links li{display:flex;align-items:center;gap:9px;height:34.3px}
.contact-row{display:flex;align-items:center;gap:12px;font-size:15px;line-height:24px;color:var(--white)}
.icon-disc{width:32px;height:32px;border-radius:50%;background:var(--white);display:flex;align-items:center;justify-content:center;flex:none}
.copyright{left:0;top:2655px;width:1200px;height:63px;border-top:1px solid #222;font-size:15px;color:var(--white);font-weight:700;text-align:center;line-height:60px}
</style>
</head>
<body>

<!-- HERO -->
<section class="abs hero">
  <div class="abs hero-scene" role="img" aria-label="Photo of Petros Vandelis speaking on stage at a conference in front of an audience"></div>
</section>

<header class="abs site-header">
  <div class="abs brand" style="left:111px;top:19px"><span class="brand-mark"></span>PETROS VANDELIS</div>
  <nav class="abs nav" style="left:0;width:1200px">
    <a class="active" style="left:585px">HOME</a>
    <a style="left:654px">ABOUT ME</a>
    <a style="left:745px">SERVICES</a>
    <a style="left:831px">TESTIMONIALS</a>
  </nav>
  <a class="abs pill" style="left:956px;top:16px;width:132px;height:46px;font-size:18px">Contact Us</a>
</header>

<h1 class="abs hero-title">I've been a digital marketer &amp;<br>an e-commerce expert<br>since 2010.</h1>
<a class="abs pill" style="left:470px;top:345px;width:225px;height:46px;font-size:17px">BOOK YOUR CONSULTATION</a>

<!-- LEAD FORM -->
<section class="abs lead-band"></section>
<div class="abs field" style="left:39px">Name</div>
<div class="abs field" style="left:228px">Email</div>
<div class="abs field" style="left:417px">Phone</div>
<div class="abs field" style="left:605px">Address</div>
<div class="abs field" style="left:794px">Services<span class="caret"></span></div>
<div class="abs field submit" style="left:983px">Submit</div>

<!-- ABOUT -->
<section class="abs about">
  <svg class="abs" style="left:0;top:0" width="1200" height="572" viewBox="0 0 1200 572">
    <polygon points="1200,49 1200,357 1008,572 755,572" fill="#1eb4ec"/>
    <polygon points="1200,378 1200,572 1016,572" fill="#0d0d0d"/>
  </svg>
  <div class="abs" style="left:600px;top:60px;width:540px;height:512px;background:radial-gradient(ellipse at 55% 45%,rgba(120,105,90,.85),rgba(70,80,110,.6) 55%,transparent 72%)" role="img" aria-label="Photo of Petros Vandelis on stage with arms spread wide, wearing a headset mic"></div>
  <h2 class="abs section-title" style="left:111px;top:67px">About Me</h2>
  <div class="abs about-text">
    <p>I Help Busy Entrepreneurs to Scale their Online Business to Multiple 7 &amp; 8 Figures Without Ever Spending a Dime on Ads. All that with the power of CRO &amp; Searchly Insights.I run a 7 figure digital marketing agency. We manage $X,XXX,XXX per month in SocialSphere &amp; Searchly ads. We are a Premier SocialSphere partner &amp; and a Searchly Premier partner. We recently scaled an ecom store to 8 figures in 75 days during Covid-19 I travel the world to speak at conferences &amp; events up to 1,000 people at a time (20 events, 15 countries, 4 continents, 10,000+ live attendees so far)</p>
    <p>&nbsp;I am the host of the Aegean Roundtable, a high-level networking mastermind event held in Zakynthos Greece twice per year (est.2017) - 100+ attendees from 34 countries.</p>
  </div>
  <a class="abs pill" style="left:112px;top:464px;width:142px;height:48px;font-size:18px">READ MORE</a>
</section>

<!-- SERVICES -->
<h2 class="abs section-title" style="left:0;width:1196px;text-align:center;top:1248px">Our Services</h2>
<div class="abs card" style="left:111px;background:radial-gradient(circle at 55% 38%,#8a6a4a,#2c3440 55%,#1a1f28)" role="img" aria-label="Hand holding a glowing globe surrounded by digital icons">
  <span class="card-label">PAID ADS</span>
</div>
<div class="abs card" style="left:444px;background:linear-gradient(135deg,#3a3a3c,#8b8e96 55%,#c8c6c2)" role="img" aria-label="Two colleagues reviewing work on a tablet">
  <span class="card-label">CONSULTING/MASTERMIND</span>
</div>
<div class="abs card" style="left:777px;background:linear-gradient(90deg,#0c1c55,#1a2c70 40%,#1a1a22 80%)" role="img" aria-label="Speaker presenting to a seated audience at a conference">
  <span class="card-label">TRAINING</span>
</div>

<!-- TESTIMONIALS -->
<section class="abs reviews"></section>
<h2 class="abs section-title" style="left:0;width:1200px;text-align:center;top:1720px">What Customer Says</h2>
<div class="abs video" role="img" aria-label="Video interview of two men seated in armchairs in a studio"></div>
<svg class="abs" style="left:378px;top:1940px" width="48" height="48" viewBox="0 0 48 48" aria-hidden="true">
  <circle cx="24" cy="24" r="21" fill="none" stroke="#1eb4ec" stroke-width="4"/>
  <polygon points="19,14 34,24 19,34" fill="#1eb4ec"/>
</svg>
<p class="abs review-text">I love Digital marketing. Although I focus a lot on CRO &amp; SI scaling (organic), I have mastered paid advertising as well.</p>
<div class="abs" style="left:730px;top:1892px;width:142px;height:139px;background:var(--blue)"></div>
<div class="abs" style="left:722px;top:1899px;width:141px;height:140px;background:linear-gradient(180deg,#d9d9d7,#3d4356)" role="img" aria-label="Portrait of a reviewer"></div>
<p class="abs quote">Itaque earum rerum hic tenetur a sapiente delectus, ut aut reiciendis voluptatibus maiores alias repellat.<br><b>-John doe</b></p>
<div class="abs stars">★★★★★</div>
<div class="abs" style="left:723px;top:2083px;font-family:var(--head);font-weight:500;font-size:15px">Five Star</div>

<svg class="abs" style="left:42px;top:2209px" width="26" height="22" viewBox="0 0 26 22" aria-hidden="true"><path d="M24 11H4M12 3L4 11l8 8" fill="none" stroke="#111" stroke-width="3"/></svg>
<svg class="abs" style="left:1122px;top:2209px" width="26" height="22" viewBox="0 0 26 22" aria-hidden="true"><path d="M2 11h20M14 3l8 8-8 8" fill="none" stroke="#111" stroke-width="3"/></svg>
<div class="abs thumb" style="left:113px" role="img" aria-label="Video testimonial thumbnail"></div>
<div class="abs thumb current" style="left:279px" role="img" aria-label="Video testimonial thumbnail, selected"></div>
<div class="abs thumb" style="left:444px" role="img" aria-label="Video testimonial thumbnail"></div>
<div class="abs thumb" style="left:610px;background:linear-gradient(135deg,#8a8a88,#b8b6b2)" role="img" aria-label="Video testimonial thumbnail"></div>
<div class="abs thumb" style="left:776px;background:linear-gradient(135deg,#6a5238,#3a3530)" role="img" aria-label="Video testimonial thumbnail"></div>
<div class="abs thumb" style="left:942px;background:linear-gradient(135deg,#5a5a5c,#9a9894)" role="img" aria-label="Video testimonial thumbnail"></div>
<svg class="abs" style="left:0;top:2203px" width="1200" height="34" viewBox="0 0 1200 34" aria-hidden="true">
  <g fill="none" stroke="#fff" stroke-width="2.5">
    <circle cx="187" cy="17" r="14"/><circle cx="353" cy="17" r="14"/><circle cx="518" cy="17" r="14"/>
    <circle cx="684" cy="17" r="14"/><circle cx="850" cy="17" r="14"/><circle cx="1016" cy="17" r="14"/>
  </g>
  <g fill="#fff">
    <polygon points="183,10 194,17 183,24"/><polygon points="349,10 360,17 349,24"/><polygon points="514,10 525,17 514,24"/>
    <polygon points="680,10 691,17 680,24"/><polygon points="846,10 857,17 846,24"/><polygon points="1012,10 1023,17 1012,24"/>
  </g>
</svg>

<!-- FOOTER -->
<footer class="abs footer"></footer>
<div class="abs brand" style="left:111px;top:2396px"><span class="brand-mark"></span>PETROS VANDELIS</div>
<span class="abs social" style="left:111px" aria-label="Social profile 1"></span>
<span class="abs social" style="left:168px" aria-label="Social profile 2"></span>
<span class="abs social" style="left:226px" aria-label="Social profile 3"></span>
<span class="abs social" style="left:283px" aria-label="Social profile 4"></span>

<h3 class="abs col-title" style="left:464px">QUICK LINK</h3>
<ul class="abs links" style="left:464px">
  <li><svg width="14" height="12" viewBox="0 0 14 12"><path d="M1 6h11M7 1l5 5-5 5" fill="none" stroke="#fff" stroke-width="2.4"/></svg>Home</li>
  <li><svg width="14" height="12" viewBox="0 0 14 12"><path d="M1 6h11M7 1l5 5-5 5" fill="none" stroke="#fff" stroke-width="2.4"/></svg>About</li>
  <li><svg width="14" height="12" viewBox="0 0 14 12"><path d="M1 6h11M7 1l5 5-5 5" fill="none" stroke="#fff" stroke-width="2.4"/></svg>Services</li>
  <li><svg width="14" height="12" viewBox="0 0 14 12"><path d="M1 6h11M7 1l5 5-5 5" fill="none" stroke="#fff" stroke-width="2.4"/></svg>Testimonials</li>
  <li><svg width="14" height="12" viewBox="0 0 14 12"><path d="M1 6h11M7 1l5 5-5 5" fill="none" stroke="#fff" stroke-width="2.4"/></svg>Contact Us</li>
</ul>

<h3 class="abs col-title" style="left:670px">HELP LINKS</h3>
<ul class="abs links" style="left:670px">
  <li><svg width="14" height="12" viewBox="0 0 14 12"><path d="M1 6h11M7 1l5 5-5 5" fill="none" stroke="#fff" stroke-width="2.4"/></svg>FAQ</li>
  <li><svg width="14" height="12" viewBox="0 0 14 12"><path d="M1 6h11M7 1l5 5-5 5" fill="none" stroke="#fff" stroke-width="2.4"/></svg>Terms of use</li>
  <li><svg width="14" height="12" viewBox="0 0 14 12"><path d="M1 6h11M7 1l5 5-5 5" fill="none" stroke="#fff" stroke-width="2.4"/></svg>Privacy Policy</li>
  <li><svg width="14" height="12" viewBox="0 0 14 12"><path d="M1 6h11M7 1l5 5-5 5" fill="none" stroke="#fff" stroke-width="2.4"/></svg>Support Links</li>
  <li><svg width="14" height="12" viewBox="0 0 14 12"><path d="M1 6h11M7 1l5 5-5 5" fill="none" stroke="#fff" stroke-width="2.4"/></svg>Conditions</li>
</ul>

<h3 class="abs col-title" style="left:876px">CONTACT US</h3>
<div class="abs contact-row" style="left:876px;top:2437px">
  <span class="icon-disc"><svg width="14" height="18" viewBox="0 0 14 18"><path d="M7 1a6 6 0 0 1 6 6c0 4-6 10-6 10S1 11 1 7a6 6 0 0 1 6-6z" fill="#111"/><circle cx="7" cy="7" r="2.2" fill="#fff"/></svg></span>
  <span>Petros Vandelis<br>United States</span>
</div>
<div class="abs contact-row" style="left:876px;top:2503px">
  <span class="icon-disc"><svg width="16" height="16" viewBox="0 0 16 16"><path d="M3 1l3 3-2 2c1 2 3 4 5 5l2-2 3 3-2 3C7 15 1 9 1 3z" fill="#111"/></svg></span>
  <span>+1 888 888 8888</span>
</div>
<div class="abs contact-row" style="left:876px;top:2555px">
  <span class="icon-disc"><svg width="16" height="12" viewBox="0 0 16 12"><rect x="0" y="0" width="16" height="12" rx="2" fill="#111"/><path d="M1 1l7 6 7-6" fill="none" stroke="#fff" stroke-width="1.5"/></svg></span>
  <span>info@petrosvandelis.com</span>
</div>

<div class="abs copyright">Copyrights@2023.Petros Vandelis.All Rights Reserved</div>

</body>
</html>
```